indépendant en tant que Massothérapeute et Préparateur Mental, j'ai besoin de ...

Massothérapeute et préparateur mental indépendant, je recherche une carte de visite sobre et dynamique, sans images liées au massage ou à la préparation mentale mais intégrant mon logo. Les couleurs que j'aime bien sont : Blanc, gris, anthracite, noir et jaune

Contact Information for Business Card

carte de préférence Horizontale
neutre qui puisse toucher le deux domaines Massothérapie et préparation mentale

Requirements
Must have
• mon projet doit intégrer au recto:
LOGO
Loïc Bardèze
078 513 26 48
info@loicbardeze.ch
et éventuellement www.loicbardeze.ch

et au verso les deux adresses:

Chemin des Ormilles 7B
1400 Yverdon-les-Bains

Route de la Gravière 9
1700 Fribourg

Should not have
• mon projet ne doit pas contenir d'image en liens avec le massage ni la préparation mentale.

```html
<!DOCTYPE html>
<html lang="fr">
<head>
<meta charset="utf-8">
<title>Loïc Bardèze – Carte de visite</title>
<link href="https://fonts.googleapis.com/css2?family=Montserrat:wght@400;500;600;700&display=swap" rel="stylesheet">
<style>
  :root {
    --anthracite: #4d4d4d;
    --anthracite-dark: #444444;
    --emboss: #474747;
    --white: #ffffff;
    --yellow: #f7bd12;
    --stage: #d9d9d9;
    --text-grey: #555555;
  }
  * { margin: 0; padding: 0; box-sizing: border-box; }
  html, body { width: 1200px; height: 965px; overflow: hidden; }
  body {
    background: var(--stage);
    font-family: "Montserrat", sans-serif;
    display: flex;
    flex-direction: column;
    align-items: center;
    justify-content: center;
    gap: 40px;
  }
  .card {
    position: relative;
    width: 640px;
    height: 414px;
    overflow: hidden;
    box-shadow: 0 6px 18px rgba(0,0,0,.18);
  }

  /* ---------- Verso (addresses) ---------- */
  .card--back { background: var(--anthracite); color: var(--white); }
  .back-watermark {
    position: absolute;
    left: 60px; top: 150px;
    font-size: 92px;
    font-weight: 600;
    color: var(--emboss);
    letter-spacing: -1px;
    white-space: nowrap;
  }
  .identity { position: absolute; display: flex; align-items: center; gap: 14px; }
  .identity__mark { width: 16px; height: 16px; border-radius: 50%; }
  .identity__name { font-weight: 600; line-height: 1; white-space: nowrap; }
  .identity__role { font-size: 10.5px; font-weight: 500; letter-spacing: .9px; text-transform: uppercase; margin-top: 6px; }

  .card--back .identity { left: 44px; top: 52px; }
  .card--back .identity__mark { background: var(--white); }
  .card--back .identity__name { font-size: 38px; color: var(--white); }
  .card--back .identity__role { color: var(--white); }

  .address {
    position: absolute;
    font-size: 17px;
    line-height: 1.35;
    font-weight: 400;
    color: var(--white);
  }
  .address--yverdon { left: 44px; bottom: 44px; text-align: right; }
  .address--fribourg { right: 44px; top: 222px; }
  .pin { position: absolute; left: 343px; top: 268px; width: 30px; height: 40px; }

  /* ---------- Recto (contact) ---------- */
  .card--front { background: var(--white); }
  .front-shape { position: absolute; inset: 0; width: 100%; height: 100%; }
  .card--front .identity { left: 40px; top: 118px; }
  .card--front .identity__mark { background: var(--anthracite); }
  .card--front .identity__name { font-size: 40px; color: var(--anthracite); }
  .card--front .identity__role { color: var(--text-grey); }

  .contact-list {
    position: absolute;
    right: 34px; top: 178px;
    list-style: none;
    color: var(--white);
    font-size: 16px;
    line-height: 1.65;
    text-align: right;
  }
  .contact-list li { display: flex; align-items: center; justify-content: flex-end; gap: 10px; }
  .contact-list svg { width: 16px; height: 16px; flex: none; }

  .signature {
    position: absolute;
    left: 40px; bottom: 34px;
    font-size: 19px;
    font-weight: 600;
    color: var(--yellow);
  }
</style>
</head>
<body>

  <!-- Verso -->
  <section class="card card--back" aria-label="Verso de la carte">
    <div class="back-watermark" aria-hidden="true">Loïc Bardèze</div>

    <div class="identity">
      <span class="identity__mark"></span>
      <div>
        <div class="identity__name">Loïc Bardèze</div>
        <div class="identity__role">Massothérapeute / Préparateur Mental</div>
      </div>
    </div>

    <svg class="pin" viewBox="0 0 30 40" aria-hidden="true">
      <path d="M15 2C8 2 3 7 3 13.5 3 22 15 37 15 37S27 22 27 13.5C27 7 22 2 15 2Z" fill="none" stroke="var(--yellow)" stroke-width="2.6"/>
      <circle cx="15" cy="13.5" r="4.5" fill="none" stroke="var(--yellow)" stroke-width="2.6"/>
    </svg>

    <address class="address address--yverdon">
      Chemin des Ormilles 7B<br>1400 Yverdon-les-Bains
    </address>
    <address class="address address--fribourg">
      Route de la Gravière 9<br>1700 Freiburg
    </address>
  </section>

  <!-- Recto -->
  <section class="card card--front" aria-label="Recto de la carte">
    <svg class="front-shape" viewBox="0 0 640 414" preserveAspectRatio="none" aria-hidden="true">
      <path d="M0 340 C170 250 380 170 640 125 L640 414 L0 414 Z" fill="var(--anthracite)"/>
      <path d="M0 332 C150 245 360 150 620 108 C390 160 180 245 0 350 Z" fill="var(--yellow)"/>
    </svg>

    <div class="identity">
      <span class="identity__mark"></span>
      <div>
        <div class="identity__name">Loïc Bardèze</div>
        <div class="identity__role">Massothérapeute / Préparateur Mental</div>
      </div>
    </div>

    <ul class="contact-list">
      <li>078 513 26 48
        <svg viewBox="0 0 16 16" aria-hidden="true"><path d="M4 2l2.5 3-1.5 1.5c.8 1.8 2.2 3.2 4 4L10.5 9l3 2.5-1.2 2C8 13.5 2.5 8 2 3.5Z" fill="none" stroke="var(--yellow)" stroke-width="1.4" stroke-linejoin="round"/></svg>
      </li>
      <li>info@loicbardeze.ch
        <svg viewBox="0 0 16 16" aria-hidden="true"><rect x="1.5" y="3.5" width="13" height="9" fill="none" stroke="var(--yellow)" stroke-width="1.4"/><path d="M1.5 3.5l6.5 5 6.5-5" fill="none" stroke="var(--yellow)" stroke-width="1.4"/></svg>
      </li>
      <li>www.loicbardeze.ch
        <svg viewBox="0 0 16 16" aria-hidden="true"><circle cx="8" cy="8" r="6.3" fill="none" stroke="var(--yellow)" stroke-width="1.4"/><ellipse cx="8" cy="8" rx="2.8" ry="6.3" fill="none" stroke="var(--yellow)" stroke-width="1.2"/><path d="M1.7 8h12.6" stroke="var(--yellow)" stroke-width="1.2"/></svg>
      </li>
    </ul>

    <div class="signature">Loïc Bardèze</div>
  </section>

</body>
</html>
```